Velk Partners Building Business Cards

We need a business card that reflects our business as "Solar Experts" in San Diego. Browse our website www.velkpartners.example our License needs to be displayed as "CSLB# 3867140" our phone number is (619) 555-0187

Save thousands on your electric bills and increase the value of your home while helping to protect the environment. Our solar installation experts will help you design the system that's right for you, using only the highest quality equipment that will look great and give you ideal performance. Our goal is to make you energy independent, and get your electric bill to 0.

Paul Osterby
(619) 555-0187
paul@velkpartners.example

Target Market(s)

Home owners in san diego looking for solar

Industry/Entity Type

Solar Energy

Contact Information for Business Card

Paul Osterby
(619) 555-0187
paul@velkpartners.example

Font styles to use
Other font styles liked:
• Use our logo font

Requirements
Must have
• License needs to be displayed as "CSLB# 3867140" our phone number is (619) 555-0187
Nice to have
• Real images of rooftop home solar in san diego
Should not have
• our business address

```html
<!DOCTYPE html>
<html lang="en">
<head>
<meta charset="utf-8">
<title>Velk Partners Building – Business Cards</title>
<link href="https://fonts.googleapis.com/css2?family=Roboto:wght@400;500;700&display=swap" rel="stylesheet">
<style>
  :root{
    --navy:#233f80;
    --navy-deep:#1f3a78;
    --navy-light:#2d4d96;
    --gold:#efa81c;
    --white:#ffffff;
    --paper:#fbfbfb;
    --ink:#2b3f6e;
    --backdrop:#a9a7a8;
  }
  *{margin:0;padding:0;box-sizing:border-box;}
  html,body{width:1200px;height:1200px;overflow:hidden;}
  body{background:var(--backdrop);font-family:'Roboto',Arial,sans-serif;position:relative;}

  .card{position:absolute;width:712px;height:418px;border-radius:22px;overflow:hidden;}
  .card--front{left:238px;top:118px;background:var(--navy);}
  .card--back{left:231px;top:644px;background:var(--paper);}

  .front__photo{position:absolute;inset:0;
    background:linear-gradient(160deg,var(--navy-light) 0%,var(--navy) 55%,var(--navy-deep) 100%);}
  .front__name{position:absolute;left:0;right:0;top:150px;text-align:center;
    color:var(--white);font-weight:700;font-size:52px;letter-spacing:-1px;}
  .front__license{position:absolute;left:0;right:0;top:364px;display:flex;justify-content:center;
    align-items:center;gap:20px;color:var(--white);font-size:18px;}
  .front__license .dash{width:55px;height:3px;background:var(--gold);}

  .back__band{position:absolute;left:0;top:0;width:712px;height:112px;
    background:linear-gradient(180deg,var(--navy) 0%,var(--navy) 82%,var(--gold) 100%);}
  .back__license{position:absolute;right:36px;top:44px;text-align:right;color:var(--white);
    font-size:18px;line-height:25px;}
  .back__name{position:absolute;left:34px;top:150px;color:var(--navy);font-weight:700;
    font-size:44px;letter-spacing:-1px;}
  .person{position:absolute;left:35px;top:322px;color:var(--navy);}
  .person__name{font-size:25px;font-weight:700;}
  .person__title{font-size:17px;margin-top:4px;color:var(--ink);}
  .contact{position:absolute;right:36px;top:306px;list-style:none;color:var(--ink);font-size:18px;}
  .contact li{display:flex;align-items:center;height:25px;}
  .contact svg{width:18px;height:18px;margin-right:14px;flex:none;}
  .contact .accent{color:var(--gold);}
</style>
</head>
<body>

<section class="card card--front">
  <div class="front__photo" role="img" aria-label="Rooftop solar panel array photo in blue tones"></div>
  <div class="front__name">Velk Partners Building</div>
  <div class="front__license"><span class="dash"></span><span>License: CSLB# 3867140</span><span class="dash"></span></div>
</section>

<section class="card card--back">
  <div class="back__band" role="img" aria-label="Decorative navy and gold wave band"></div>
  <div class="back__license">License:<br>CSLB# 3867140</div>
  <div class="back__name">Velk Partners Building</div>
  <div class="person">
    <div class="person__name">Paul Osterby</div>
    <div class="person__title">Managing Director</div>
  </div>
  <ul class="contact">
    <li><svg viewBox="0 0 20 20"><path d="M2 8c0-3 4-5 8-5s8 2 8 5l-3 1-1-2c-2-1-6-1-8 0l-1 2z" fill="var(--gold)"/><rect x="4" y="10" width="12" height="8" rx="1" fill="var(--gold)"/></svg>(619) 555-0187</li>
    <li><svg viewBox="0 0 20 20"><circle cx="10" cy="10" r="8" fill="none" stroke="var(--gold)" stroke-width="1.8"/><ellipse cx="10" cy="10" rx="3.5" ry="8" fill="none" stroke="var(--gold)" stroke-width="1.5"/><path d="M2 10h16M4 6h12M4 14h12" stroke="var(--gold)" stroke-width="1.3"/></svg>paul@velkpartners.example</li>
    <li><svg viewBox="0 0 20 20"><rect x="1.5" y="4" width="17" height="12" fill="var(--gold)"/><path d="M1.5 4l8.5 7 8.5-7" fill="none" stroke="var(--white)" stroke-width="1.4"/></svg>www.<span class="accent">velkpartners</span>.example</li>
  </ul>
</section>

</body>
</html>
```